New Bicycle shop business card

Hi!
I'm looking for a business card for my new proffesional bike mechanics shop. This shop is only for fixing broken bikes and not selling bikes.
Peferbly a modern and sleek and modern design.
Colors: black, grey, red, white
Information:
Name: Rijwielwerkplaats Vanhoutte
Shop owner: Bart Vanhoutte & Marieke Segers
Website: www.rijwielwerkplaats-vanhoutte.be
Email: info@rijwielwerkplaats-vanhoutte.be
Phone number: +32471902368
Street adres: Kerkweg 46
9940 Bellebeke
Slogan/shop information: Herstellingen van alle merken.
Logo: see files.
Target Market(s)
People who seek a mechanic to fix or upgrade their bikes.
Contact Information for Business Card
Information:
Website: info@rijwielwerkplaats-vanhoutte.be
9940 Bellebeke
Logo: see files.

```html
<!DOCTYPE html>
<html lang="nl">
<head>
<meta charset="utf-8">
<title>Rijwielwerkplaats Vanhoutte – Visitekaartje</title>
<link href="https://fonts.googleapis.com/css2?family=Lato:wght@400;700;900&display=swap" rel="stylesheet">
<style>
  :root {
    --backdrop: #2b2b2d;
    --card: #141414;
    --card-edge: #1d1d1d;
    --red: #e3173e;
    --white: #ffffff;
    --grey: #c9c9c9;
    --rule: #4a4a4a;
  }
  * { margin: 0; padding: 0; box-sizing: border-box; }
  html, body {
    width: 1200px; height: 900px; overflow: hidden;
    background: var(--backdrop);
    font-family: "Lato", sans-serif;
  }
  .stage {
    width: 1200px; height: 900px;
    display: flex; flex-direction: column; align-items: center; justify-content: center;
    gap: 50px;
  }
  .card {
    position: relative;
    width: 560px; height: 320px;
    background: linear-gradient(160deg, var(--card-edge), var(--card));
    overflow: hidden;
    display: flex; flex-direction: column; align-items: center; justify-content: center;
  }
  .card__band {
    position: absolute; left: 0; right: 0; bottom: 0;
    height: 12px; background: var(--red);
  }

  /* Front */
  .brand { display: flex; flex-direction: column; align-items: center; gap: 16px; margin-top: -12px; }
  .brand__mark { width: 46px; height: 46px; background: var(--red); }
  .brand__name {
    color: var(--white); font-weight: 900; text-transform: uppercase;
    text-align: center; font-size: 34px; line-height: 1.05; letter-spacing: 1px;
  }

  /* Back */
  .contact { text-align: center; margin-top: -14px; }
  .contact__owners {
    color: var(--red); font-size: 21px; font-weight: 400; text-transform: uppercase;
    letter-spacing: 0.3px;
  }
  .contact__role { color: var(--grey); font-size: 13px; margin-top: 2px; }
  .contact__rule { width: 160px; height: 1px; background: var(--rule); margin: 8px auto; }
  .contact__line { color: var(--white); font-size: 15px; line-height: 1.35; }
  .contact__label { color: var(--red); font-weight: 700; margin-right: 3px; }
  .contact__address { color: var(--white); font-size: 16px; }
</style>
</head>
<body>
<main class="stage">
  <section class="card card--front">
    <div class="brand">
      <div class="brand__mark"></div>
      <div class="brand__name">Rijwielwerkplaats<br>Vanhoutte</div>
    </div>
    <div class="card__band"></div>
  </section>

  <section class="card card--back">
    <div class="contact">
      <p class="contact__owners">Bart Vanhoutte &amp; Marieke Segers</p>
      <p class="contact__role">Owner</p>
      <div class="contact__rule"></div>
      <p class="contact__line"><span class="contact__label">P:</span>+32471902368</p>
      <p class="contact__line"><span class="contact__label">P:</span>info@rijwielwerkplaats-vanhoutte.be</p>
      <p class="contact__line"><span class="contact__label">W:</span>www.rijwielwerkplaats-vanhoutte.be</p>
      <div class="contact__rule"></div>
      <p class="contact__address">Kerkweg 46 9940 Bellebeke</p>
    </div>
    <div class="card__band"></div>
  </section>
</main>
</body>
</html>
```